CONTEMPORARY Canva Art Design for Christians

I need a canvas art design on Christianity. The design must be in 3 SIMPLE dimensions: 12x 18 inches / 28 x 24 inches / 30 x 40 inches
The design must be accompanied by christian quote.
The christian quote can be "As For Me And My House We Will Serve The Lord (Joshua 24:15)" or any other quote that is good for display in a christian home.

I DON'T WANT THE TRADITIONAL CHRISTIAN DESIGN.. I WANT COLOURFUL, MEANINGFUL and CONTEMPORARY, MODERN DESIGN. And stay away from the scary image of Jesus in dark background, it only makes the home more scary not holy!

Target Market(s)

Christians

Colors

Designer to choose colors to be used in the design.

Requirements
Must have
• A graphic design and a christian quote that is powerful and edifies the soul. Great for display at home. Great use of colours to enhance the message.
Nice to have
• I wish to see great unique design with strong use of colours, images to enhance the scripture. It must glorify Jesus.
Should not have
• Should not be dull.

```html
<!DOCTYPE html>
<html lang="en">
<head>
<meta charset="utf-8">
<title>As For Me And My House — Scripture Canvas</title>
<link href="https://fonts.googleapis.com/css2?family=Francois+One&family=Libre+Caslon+Text&display=swap" rel="stylesheet">
<style>
  :root {
    --page: #f2f2f0;
    --ink-white: #ffffff;
    --shadow: rgba(40, 25, 0, 0.75);
    --sky-blue: #4f8fb8;
    --leaf-green: #4e9a2a;
    --sun-yellow: #f4e21a;
    --gold: #e8b318;
    --wheat: #b8862a;
    --amber: #e07a10;
    --rust: #9a4a12;
    --robe: #e9dcc0;
  }
  * { margin: 0; padding: 0; box-sizing: border-box; }
  html, body {
    width: 1200px; height: 737px; overflow: hidden;
    background: var(--page);
  }
  .canvas-art {
    position: absolute;
    left: 60px; top: 6px;
    width: 1080px; height: 725px;
    overflow: hidden;
  }
  .scene {
    position: absolute; inset: 0;
    background:
      radial-gradient(ellipse 30% 35% at 88% 28%, rgba(140,110,40,0.55), transparent 70%),
      radial-gradient(ellipse 40% 30% at 22% 42%, rgba(255,240,150,0.95), transparent 70%),
      radial-gradient(ellipse 45% 40% at 92% 85%, var(--rust), transparent 75%),
      linear-gradient(175deg, var(--leaf-green) 0%, var(--sky-blue) 22%, var(--gold) 42%, var(--wheat) 62%, #8a6018 100%),
      linear-gradient(90deg, transparent 50%, var(--sun-yellow) 70%, var(--amber) 100%);
    background-blend-mode: normal, screen, normal, normal, overlay;
  }
  .scene-warm {
    position: absolute; inset: 0;
    background: linear-gradient(100deg, transparent 45%, rgba(250,220,20,0.75) 62%, rgba(230,120,15,0.8) 85%, rgba(150,70,20,0.85) 100%);
  }
  .figure {
    position: absolute;
    left: 110px; top: 376px;
    width: 282px; height: 349px;
    border-radius: 120px 120px 0 0;
    background: linear-gradient(180deg, #7a5a30 0%, var(--robe) 30%, #d8c69c 100%);
    opacity: 0.9;
  }
  .quote {
    position: absolute; inset: 0;
    font-family: "Francois One", "Arial Narrow", sans-serif;
    font-weight: 400;
    color: var(--ink-white);
    text-shadow: 3px 4px 6px var(--shadow);
    line-height: 1;
  }
  .quote span { position: absolute; white-space: nowrap; }
  .line-1       { left: 163px; top: 71px;  font-size: 118px; }
  .line-2-small { left: 258px; top: 248px; font-size: 72px; }
  .line-2       { left: 396px; top: 203px; font-size: 124px; }
  .line-3-small { left: 330px; top: 367px; font-size: 80px; }
  .line-3       { left: 445px; top: 330px; font-size: 123px; }
  .line-4       { left: 375px; top: 432px; font-size: 157px; }
  .reference {
    position: absolute;
    left: 652px; top: 612px;
    font-family: "Libre Caslon Text", Georgia, serif;
    font-variant: small-caps;
    font-size: 50px;
    line-height: 1;
    color: var(--ink-white);
    letter-spacing: 0.5px;
    white-space: nowrap;
  }
</style>
</head>
<body>
  <main class="canvas-art">
    <div class="scene" role="img" aria-label="Sunrise over a golden wheat field with blue sky, green leaves and a sunflower"></div>
    <div class="scene-warm"></div>
    <div class="figure" role="img" aria-label="A robed shepherd cradling a lamb among the wheat"></div>
    <h1 class="quote">
      <span class="line-1">As For Me</span>
      <span class="line-2-small">And</span>
      <span class="line-2">My House</span>
      <span class="line-3-small">We</span>
      <span class="line-3">Will Serve</span>
      <span class="line-4">The LORD.</span>
    </h1>
    <p class="reference">(Joshua 24:15)</p>
  </main>
</body>
</html>
```